House flipping business web site needed

pinecrestholdingsgroup.example.
I am a residential developer in Northern NJ and I am looking for a fresh new updated website. I have an intro video about my company being made now. I don't update it very often but I want an easy format that I can add update photos to on projects I have worked on or homes I renovate for sale.

Target Market(s)

investors into my projects so a portfolio , people looking to sell their homes to me.

Industry/Entity Type

Real Estate Development

Number of Pages Required

4 page

Font styles to use
Serif

Colors
33b8a4
39a9d7
cadf82

Requirements
Must have
• space for an intro video about my company
• a portfolio with pictures and information about each project
• Markets we serve- Morris County, NJ
• My logo- already created
• SEO
• Yes I would like this to function over all platforms. Phone, computer, all platforms.
• history and background page
• I am looking for a completed page that I can upload to the site that hosts my website
Nice to have
• I want something creative, easy to navigate. modern.

```html
<!DOCTYPE html>
<html lang="en">
<head>
<meta charset="utf-8">
<title>Pinecrest Holdings Group</title>
<link href="https://fonts.googleapis.com/css2?family=Raleway:wght@300;400;500&family=Open+Sans:wght@400;600;700&family=Roboto+Condensed:wght@400&display=swap" rel="stylesheet">
<style>
:root{
  --blue:#2a7fc0;
  --sky:#2ea3dc;
  --ink:#555a60;
  --dark:#4a4a50;
  --navy:#1a2333;
  --white:#ffffff;
}
*{margin:0;padding:0;box-sizing:border-box}
h1,h2,h3,h4{font-weight:400}
html,body{width:1200px;height:2456px;overflow:hidden;background:var(--white)}
body{font-family:"Open Sans",sans-serif;color:var(--ink)}
.page{position:relative;width:1200px;height:2456px;overflow:hidden}

.site-header{position:absolute;left:0;top:0;width:1200px;height:140px;background:var(--white)}
.brand{position:absolute;left:77px;top:0;width:260px;height:208px;background:var(--white);z-index:3;display:flex;flex-direction:column;align-items:center;justify-content:center;gap:10px}
.brand-square{width:70px;height:70px;background:var(--sky)}
.brand-name{font-family:"Raleway",sans-serif;font-weight:500;font-size:24px;color:var(--blue);text-align:center;line-height:1.15}
.main-nav a{position:absolute;top:40px;font-family:"Raleway",sans-serif;font-size:24px;color:#444;text-decoration:none;letter-spacing:.5px}
.main-nav a.active{color:var(--blue)}

.hero{position:absolute;left:0;top:140px;width:1200px;height:522px;background:linear-gradient(180deg,#3e5a2a 0%,#6b7a5c 40%,#8a8578 55%,#4e7a2c 80%,#5f9a32 100%)}

.tagline-band{position:absolute;left:0;top:662px;width:1200px;height:104px;background:var(--sky)}
.tagline{position:absolute;left:80px;top:31px;font-family:"Roboto Condensed",sans-serif;font-size:30px;color:var(--white)}
.btn-white{position:absolute;left:930px;top:26px;width:193px;height:52px;background:var(--white);border-radius:3px;color:var(--sky);font-family:"Raleway",sans-serif;font-size:23px;display:flex;align-items:center;justify-content:center}

.section-title{position:absolute;left:0;width:1200px;text-align:center;font-family:"Raleway",sans-serif;font-weight:300;font-size:42px;color:#555}
.section-title span{color:var(--blue);font-weight:400}
.intro-text{position:absolute;left:0;width:1200px;text-align:center;font-size:15.5px;line-height:25px}

.feature-icon{position:absolute;width:104px;height:104px;border:2px solid var(--sky);border-radius:50%;display:flex;align-items:center;justify-content:center;color:var(--sky)}
.feature-title{position:absolute;font-family:"Raleway",sans-serif;font-weight:400;font-size:24px;color:var(--sky)}
.feature-text{position:absolute;font-size:15.5px;line-height:25px;width:232px}

.portfolio{position:absolute;left:0;top:1168px;width:1200px;height:540px;background:linear-gradient(180deg,#2a3446 0%,#1d2738 45%,#3a3a30 75%,#151c28 100%)}
.portfolio .section-title{color:var(--white)}
.portfolio .section-title span{color:var(--sky)}
.project-photo{position:absolute;top:128px;width:234px;height:154px;border:3px solid #e8e8e8}
.project-title{position:absolute;top:292px;width:234px;text-align:center;font-family:"Raleway",sans-serif;font-size:24px;color:var(--white)}
.project-text{position:absolute;top:322px;width:250px;text-align:center;font-size:15.5px;line-height:26px;color:var(--white)}
.project-more{position:absolute;top:380px;width:234px;text-align:center;font-size:16px;color:var(--white)}
.btn-blue{position:absolute;background:var(--blue);color:var(--white);border-radius:3px;font-family:"Raleway",sans-serif;font-size:21px;display:flex;align-items:center;justify-content:center}

.video-frame{position:absolute;left:74px;top:1778px;width:478px;height:311px;background:#c8c8c8;padding:10px}
.video-still{width:100%;height:100%;background:linear-gradient(180deg,#2e3a2a 0%,#5a6470 45%,#4a4f48 75%,#6a6a66 100%);display:flex;align-items:center;justify-content:center}
.about-title{position:absolute;left:602px;top:1772px;font-family:"Raleway",sans-serif;font-weight:300;font-size:42px;color:#555}
.about-title span{color:var(--blue);font-weight:400}
.about-text{position:absolute;left:602px;width:520px;font-size:15.5px;line-height:26px}

.site-footer{position:absolute;left:0;top:2150px;width:1200px;height:253px;background:var(--dark);color:#ddd}
.footer-brand{position:absolute;left:98px;top:44px;width:197px;height:163px;display:flex;flex-direction:column;align-items:center;justify-content:center;gap:12px}
.footer-brand .brand-square{width:56px;height:56px}
.footer-brand .brand-name{color:var(--white);font-size:22px}
.footer-heading{position:absolute;top:30px;font-family:"Raleway",sans-serif;font-weight:400;font-size:23px;color:var(--white)}
.footer-link{position:absolute;left:350px;font-size:17px;color:#ccc}
.footer-link.active{color:var(--white)}
.contact-line{position:absolute;left:607px;width:268px;font-size:15.5px;line-height:24px;color:var(--white);display:flex;gap:12px}
.contact-line svg{flex:none;margin-top:4px}
.contact-line span{min-width:0;overflow-wrap:anywhere}
.contact-email{font-size:14.5px;line-height:22px}
.newsletter-text{position:absolute;left:890px;top:70px;width:240px;font-size:15.5px;line-height:24px;color:var(--white)}
.email-field{position:absolute;left:889px;top:122px;width:234px;height:36px;background:var(--white);color:#666;font-size:15px;padding:7px 8px}
.btn-subscribe{position:absolute;left:889px;top:168px;width:160px;height:42px;background:var(--sky);color:var(--white);font-family:"Raleway",sans-serif;font-size:21px;display:flex;align-items:center;justify-content:center}

.copyright{position:absolute;left:0;top:2403px;width:1200px;height:53px;background:var(--sky);color:var(--white);font-size:15.5px;display:flex;align-items:center;justify-content:center}
.copyright b{font-weight:700}
</style>
</head>
<body>
<div class="page">

  <header class="site-header">
    <div class="brand">
      <div class="brand-square"></div>
      <div class="brand-name">PINECREST<br>HOLDINGS GROUP</div>
    </div>
    <nav class="main-nav">
      <a class="active" style="left:568px">HOME</a>
      <a style="left:683px">ABOUT</a>
      <a style="left:812px">PORTFOLIO</a>
      <a style="left:995px">CONTACT</a>
    </nav>
  </header>

  <div class="hero" role="img" aria-label="Photo of a weathered single-storey house in a wooded lot before renovation"></div>

  <section class="tagline-band">
    <p class="tagline">We bring excellence to the home buying and renovation business.</p>
    <div class="btn-white">CONTACT US</div>
  </section>

  <section class="welcome">
    <h1 class="section-title" style="top:806px">WELCOME TO <span>PINECREST HOLDINGS GROUP</span></h1>
    <p class="intro-text" style="top:872px">We only buy and renovate homes in our neighborhoods right here in the Morris County, NJ area.</p>
    <p class="intro-text" style="top:922px">Is a house in your neighborhood an eyesore? Is it vacant, boarded up and a hazard to the neighborhood? Please contact us and we can help<br>transform that property into a beautiful home.</p>

    <div class="feature-icon" style="left:77px;top:1001px">
      <svg width="44" height="60" viewBox="0 0 44 60"><text x="22" y="52" text-anchor="middle" font-family="Open Sans,sans-serif" font-weight="700" font-size="60" fill="#2ea3dc">?</text></svg>
    </div>
    <h3 class="feature-title" style="left:192px;top:999px">How we can help</h3>
    <p class="feature-text" style="left:192px;top:1036px">Do you need to sell your home fast to avoid fore closure, have estate home...</p>

    <div class="feature-icon" style="left:439px;top:1001px">
      <svg width="44" height="54" viewBox="0 0 44 54" fill="none" stroke="#2ea3dc" stroke-width="3"><path d="M4 2h26l10 10v40H4z"/><path d="M30 2v10h10"/><path d="M12 30h20M12 38h20M12 46h20"/><text x="16" y="24" font-family="Open Sans,sans-serif" font-size="16" font-weight="700" fill="#2ea3dc" stroke="none" text-anchor="middle">$</text></svg>
    </div>
    <h3 class="feature-title" style="left:553px;top:999px">Financing</h3>
    <p class="feature-text" style="left:553px;top:1036px">Lorem Ipsum is simply dummy text of the printing and typesetting industry...</p>

    <div class="feature-icon" style="left:796px;top:1001px">
      <svg width="54" height="54" viewBox="0 0 54 54" fill="#2ea3dc"><circle cx="20" cy="32" r="13"/><circle cx="20" cy="32" r="5" fill="#fff"/><g fill="#2ea3dc"><rect x="17" y="14" width="6" height="6"/><rect x="17" y="44" width="6" height="6"/><rect x="2" y="29" width="6" height="6"/><rect x="32" y="29" width="6" height="6"/></g><circle cx="40" cy="14" r="8"/><circle cx="40" cy="14" r="3" fill="#fff"/></svg>
    </div>
    <h3 class="feature-title" style="left:910px;top:999px">What we do</h3>
    <p class="feature-text" style="left:910px;top:1036px">We are a team of experienced home buyers and renovators in the Morris...</p>
  </section>

  <section class="portfolio" role="img" aria-label="Dusk city skyline with a yellow bridge over a river, darkened behind the portfolio">
    <h2 class="section-title" style="top:62px">RECENT <span>PORTFOLIO</span></h2>

    <div class="project-photo" style="left:77px;background:linear-gradient(180deg,#9cb0c4,#7a8a7e 60%,#5a6a3a)" role="img" aria-label="Renovated grey two-storey house"></div>
    <div class="project-title" style="left:77px">TITLE</div>
    <p class="project-text" style="left:69px">Lorem Ipsum is simply dummy<br>text of the printing...</p>
    <div class="project-more" style="left:77px">READ MORE &raquo;</div>

    <div class="project-photo" style="left:347px;background:linear-gradient(180deg,#a8bcd0,#9a7a5a 50%,#7a5a3a)" role="img" aria-label="House under construction with exposed sheathing"></div>
    <div class="project-title" style="left:347px">TITLE</div>
    <p class="project-text" style="left:339px">Lorem Ipsum is simply dummy<br>text of the printing...</p>
    <div class="project-more" style="left:347px">READ MORE &raquo;</div>

    <div class="project-photo" style="left:617px;background:linear-gradient(180deg,#d8d8d6,#8a8a88 55%,#4a3a30)" role="img" aria-label="Renovated open-plan living room and kitchen"></div>
    <div class="project-title" style="left:617px">TITLE</div>
    <p class="project-text" style="left:609px">Lorem Ipsum is simply dummy<br>text of the printing...</p>
    <div class="project-more" style="left:617px">READ MORE &raquo;</div>

    <div class="project-photo" style="left:887px;background:linear-gradient(180deg,#6a7a8a,#8a8a90 45%,#e8ecf0)" role="img" aria-label="Small property lot in winter snow"></div>
    <div class="project-title" style="left:887px">TITLE</div>
    <p class="project-text" style="left:879px">Lorem Ipsum is simply dummy<br>text of the printing...</p>
    <div class="project-more" style="left:887px">READ MORE &raquo;</div>

    <div class="btn-blue" style="left:525px;top:423px;width:149px;height:49px">VIEW ALL</div>
  </section>

  <section class="about">
    <div class="video-frame">
      <div class="video-still" role="img" aria-label="Company intro video still showing a renovated grey house">
        <svg width="56" height="40" viewBox="0 0 56 40"><rect width="56" height="40" rx="10" fill="rgba(0,0,0,.55)"/><path d="M22 11l14 9-14 9z" fill="#fff"/></svg>
      </div>
    </div>
    <h2 class="about-title">ABOUT <span>US</span></h2>
    <p class="about-text" style="top:1834px">Pinecrest Holdings Group is a family run business with 3rd generation builders and renovators in the Morris County area. As the President and owner of Pinecrest Holdings Group I am dedicated to working hard to create opportunities for investment through real estate.</p>
    <p class="about-text" style="top:1962px">At Pinecrest Holdings Group we have a valuable support system and a team of investors, realtors, attorneys, contractors and property...</p>
    <div class="btn-blue" style="left:599px;top:2035px;width:166px;height:51px">READ MORE</div>
  </section>

  <footer class="site-footer">
    <div class="footer-brand">
      <div class="brand-square"></div>
      <div class="brand-name">PINECREST<br>HOLDINGS GROUP</div>
    </div>

    <h4 class="footer-heading" style="left:350px">USEFUL LINKS</h4>
    <div class="footer-link active" style="top:72px">Home</div>
    <div class="footer-link" style="top:108px">About</div>
    <div class="footer-link" style="top:144px">Portfolio</div>
    <div class="footer-link" style="top:182px">Services</div>

    <h4 class="footer-heading" style="left:607px">KEEP IN TOUCH</h4>
    <div class="contact-line" style="top:70px">
      <svg width="14" height="20" viewBox="0 0 14 20"><path d="M7 0a7 7 0 0 1 7 7c0 5-7 13-7 13S0 12 0 7a7 7 0 0 1 7-7z" fill="#fff"/><circle cx="7" cy="7" r="2.6" fill="#4a4a50"/></svg>
      <span>Morris County, NJ |<br>862-555-PINE (7463)</span>
    </div>
    <div class="contact-line" style="top:132px">
      <svg width="18" height="18" viewBox="0 0 18 18"><path d="M4 1l3 4-2 2c1 2.5 3.5 5 6 6l2-2 4 3-2 3C8 17 1 10 1 3z" fill="#fff"/></svg>
      <span>123 456 7890</span>
    </div>
    <div class="contact-line" style="top:168px">
      <svg width="18" height="14" viewBox="0 0 18 14" fill="none" stroke="#fff" stroke-width="1.6"><rect x="1" y="1" width="16" height="12"/><path d="M1 1l8 7 8-7"/></svg>
      <span class="contact-email">info@<wbr>pinecrestholdingsgroup.example</span>
    </div>

    <h4 class="footer-heading" style="left:890px">NEWSLETTER</h4>
    <p class="newsletter-text">Subscribe to stay on Pinecrest Holdings Group</p>
    <div class="email-field">Enter Email id</div>
    <div class="btn-subscribe">SUBSCRIBE</div>
  </footer>

  <div class="copyright">©&nbsp;<b>Pinecrest Holdings Group</b>&nbsp;- 2016. All Rights Reserved.</div>

</div>
</body>
</html>
```